We are a recruitment company based in Norwich/Cambridge England.
I have included our company logo which we want to remain the same.

What we are looking for is a new creative Business card which will really stand out!!

Contact Information for Business Card

Harriet Dunmore
email: Harriet@plavex.co.uk
Address: Brackwell House
Fenmoor Enterprise Park
Partridge Way
Norwich
QB9 3KX
Tel:01632 960418

```html
<!DOCTYPE html>
<html lang="en">
<head>
<meta charset="utf-8">
<title>Plavex Business Card</title>
<link rel="stylesheet" href="https://fonts.googleapis.com/css2?family=Open+Sans:wght@400;600;700&display=swap">
<style>
  :root {
    --lime: #8cc63f;
    --lime-deep: #7db535;
    --slate: #8e8a8f;
    --slate-text: #807c82;
    --ink: #3a3a3c;
    --paper: #ffffff;
    --backdrop: #e9e8ea;
  }
  * { box-sizing: border-box; margin: 0; padding: 0; }
  html, body {
    width: 1200px; height: 900px; overflow: hidden;
    background: var(--backdrop);
    font-family: "Open Sans", Arial, sans-serif;
  }
  .canvas {
    width: 1200px; height: 900px;
    display: flex; flex-direction: column; align-items: center; justify-content: center; gap: 44px;
  }
  .card {
    position: relative; width: 640px; height: 366px;
    border-radius: 22px; overflow: hidden;
    box-shadow: 0 10px 28px rgba(0,0,0,.18);
  }
  .card-front { background: var(--paper); }
  .front-art { position: absolute; inset: 0; }
  .brand { position: absolute; display: flex; align-items: center; gap: 14px; }
  .brand-dot { border-radius: 50%; }
  .brand-name { font-weight: 600; letter-spacing: -0.5px; line-height: 1; }
  .card-front .brand { left: 62px; top: 138px; }
  .card-front .brand-dot { width: 48px; height: 48px; background: var(--lime); }
  .card-front .brand-name { font-size: 46px; color: var(--lime); }
  .person { position: absolute; left: 118px; top: 226px; }
  .person-name { font-size: 19px; font-weight: 700; color: var(--slate-text); letter-spacing: .3px; }
  .person-role { font-size: 16px; color: var(--lime); margin-top: 1px; }
  .contacts { position: absolute; left: 138px; top: 284px; list-style: none; }
  .contacts li { display: flex; align-items: center; gap: 9px; font-size: 15px; color: var(--ink); line-height: 22px; }
  .contacts svg { width: 11px; height: 11px; fill: var(--lime); flex: none; }
  .address { position: absolute; left: 362px; top: 232px; font-style: normal; font-size: 14.5px; line-height: 21px; color: var(--ink); }
  .address span { display: block; }
  .address span:nth-child(2) { padding-left: 12px; }
  .address span:nth-child(3) { padding-left: 24px; }
  .card-back { background: linear-gradient(150deg, var(--lime) 0%, var(--lime-deep) 30%, #9ea67f 60%, var(--slate) 85%); }
  .card-back .brand { left: 50%; top: 50%; transform: translate(-50%, -50%); gap: 20px; }
  .card-back .brand-dot { width: 74px; height: 74px; border: 12px solid var(--paper); }
  .card-back .brand-name { font-size: 62px; color: var(--paper); }
</style>
</head>
<body>
<main class="canvas">
  <section class="card card-front" aria-label="Card front">
    <svg class="front-art" viewBox="0 0 640 366" aria-hidden="true">
      <path class="corner-band" fill="var(--slate)" d="M300,0 H640 V366 H560 Z"/>
      <ellipse class="arc-band" fill="var(--lime)" cx="300" cy="300" rx="360" ry="320"/>
      <ellipse class="field" fill="var(--paper)" cx="300" cy="300" rx="330" ry="290"/>
    </svg>
    <div class="brand">
      <span class="brand-dot"></span>
      <span class="brand-name">Plavex</span>
    </div>
    <div class="person">
      <p class="person-name">HARRIET DUNMORE</p>
      <p class="person-role">President</p>
    </div>
    <ul class="contacts">
      <li><svg viewBox="0 0 24 24"><path d="M6.6 10.8a15 15 0 0 0 6.6 6.6l2.2-2.2a1 1 0 0 1 1-.25 11.4 11.4 0 0 0 3.6.57 1 1 0 0 1 1 1V20a1 1 0 0 1-1 1A17 17 0 0 1 3 4a1 1 0 0 1 1-1h3.5a1 1 0 0 1 1 1c0 1.25.2 2.45.57 3.57a1 1 0 0 1-.25 1z"/></svg>01632 960418</li>
      <li><svg viewBox="0 0 24 24"><path d="M2 5h20v14H2z M2 5l10 8 10-8" stroke="#fff" stroke-width="1.5"/></svg>harriet@plavex.co.uk</li>
      <li><svg viewBox="0 0 24 24"><circle cx="12" cy="12" r="11"/></svg>www.plavex.co.uk</li>
    </ul>
    <address class="address">
      <span>Brackwell House</span>
      <span>Fenmoor Enterprise Park</span>
      <span>Partridge Way Norwich QB9 3KX</span>
    </address>
  </section>

  <section class="card card-back" aria-label="Card back">
    <div class="brand">
      <span class="brand-dot"></span>
      <span class="brand-name">Plavex</span>
    </div>
  </section>
</main>
</body>
</html>
```